High value cover design for an A4 ideation pad.

The product is NOT A BOOK.

It's an A4 ideation pad for professionals, designers and creators who handwrite their ideas. Visualise creators like Milo Varnet, Owen Plaskit and Gregor Lunwick in your mind's eye.

I'm looking for a cover design for the ideation pad. Both front and back.

It should look, feel and convey the following.

--> A handcrafted product experience

--> High value & Elegance

--> Inspiration

Mandatory --> See Uploaded Files --> Files 1, 5 & 6

Target Market(s)

- Designers

-Creative Professionals

- Entrepreneurs

who handwrite their ideas. Visualise creators like Milo Varnet, Owen Plaskit and Gregor Lunwick in your mind's eye.

Industry/Entity Type

Stationary

Font styles to use
Script
Other font styles liked:
• Calligraphy

Colors
fbed22

Requirements
Must have
• Title text - Quiet Kettle Notes

-Text in gold on brown leather background to convey high value for the front cover.

--> High value & Elegance

--> Inspiration

--> Should compel the customers to pick up and own the idea pad
Nice to have
• That's my take but other ideas are welcome
Should not have
• Must not convey

- low value

```html
<!DOCTYPE html>
<html lang="en">
<head>
<meta charset="utf-8">
<title>Quiet Kettle Notes — A4 Ideation Pad Covers</title>
<link rel="stylesheet" href="https://fonts.googleapis.com/css2?family=Allura&display=swap">
<style>
  :root {
    --backdrop: #f2f0eb;
    --leather-light: #9a5a35;
    --leather-mid: #7c4228;
    --leather-dark: #5a2c1c;
    --foil-gold: #e3b54c;
    --foil-gold-soft: #d9a843;
    --cover-shadow: rgba(40, 25, 15, 0.28);
  }
  * { margin: 0; padding: 0; box-sizing: border-box; }
  html, body {
    width: 1200px;
    height: 826px;
    overflow: hidden;
    background: var(--backdrop);
  }
  .canvas {
    position: relative;
    width: 1200px;
    height: 826px;
  }
  .pad-cover {
    position: absolute;
    top: 76px;
    width: 450px;
    height: 635px;
    box-shadow: 3px 4px 10px var(--cover-shadow);
    overflow: hidden;
  }
  .pad-cover--front { left: 76px; }
  .pad-cover--back { left: 678px; }
  .leather-surface {
    position: absolute;
    inset: 0;
  }
  .pad-cover--front .leather-surface {
    background:
      radial-gradient(ellipse at 40% 20%, rgba(190, 120, 75, 0.45), transparent 60%),
      linear-gradient(180deg, var(--leather-light) 0%, var(--leather-mid) 55%, var(--leather-dark) 100%);
  }
  .pad-cover--back .leather-surface {
    background:
      radial-gradient(ellipse at 60% 45%, rgba(90, 40, 25, 0.35), transparent 65%),
      linear-gradient(180deg, var(--leather-mid) 0%, #6e3826 50%, var(--leather-mid) 100%);
  }
  .title-mark {
    position: absolute;
    display: flex;
    flex-direction: column;
    align-items: center;
    font-family: "Allura", cursive;
    color: var(--foil-gold);
    line-height: 1;
  }
  .title-mark__word { display: block; }
  .title-mark__rule {
    display: block;
    height: 1px;
    background: var(--foil-gold-soft);
  }
  .pad-cover--front .title-mark {
    left: 0; right: 0;
    top: 218px;
  }
  .pad-cover--front .title-mark__word--lead { font-size: 46px; }
  .pad-cover--front .title-mark__word--link { font-size: 26px; margin-top: 6px; }
  .pad-cover--front .title-mark__word--close { font-size: 46px; margin-top: 4px; }
  .pad-cover--front .title-mark__rule { width: 132px; margin-top: 18px; }

  .pad-cover--back .title-mark {
    left: 0; right: 0;
    top: 510px;
    transform: translateX(74px);
  }
  .pad-cover--back .title-mark__word--lead { font-size: 28px; }
  .pad-cover--back .title-mark__word--link { font-size: 16px; margin-top: 3px; }
  .pad-cover--back .title-mark__word--close { font-size: 28px; margin-top: 2px; }
  .pad-cover--back .title-mark__rule { width: 80px; margin-top: 10px; }
</style>
</head>
<body>
<main class="canvas">
  <section class="pad-cover pad-cover--front" aria-label="Front cover">
    <div class="leather-surface" role="img" aria-label="Brown leather texture surface"></div>
    <h1 class="title-mark">
      <span class="title-mark__word title-mark__word--lead">Quiet</span>
      <span class="title-mark__word title-mark__word--link">Kettle</span>
      <span class="title-mark__word title-mark__word--close">Notes</span>
      <span class="title-mark__rule" aria-hidden="true"></span>
    </h1>
  </section>

  <section class="pad-cover pad-cover--back" aria-label="Back cover">
    <div class="leather-surface" role="img" aria-label="Brown leather texture surface"></div>
    <p class="title-mark">
      <span class="title-mark__word title-mark__word--lead">Quiet</span>
      <span class="title-mark__word title-mark__word--link">Kettle</span>
      <span class="title-mark__word title-mark__word--close">Notes</span>
      <span class="title-mark__rule" aria-hidden="true"></span>
    </p>
  </section>
</main>
</body>
</html>
```